One of Australia's fastest growing energy maintenance contractors needs a new website

www.brightleaf.com.au
Our business has evolved over the past years and now our website is no longer relevant.
We clean solar panels and we vacuum roof gutters.
We clean solar panels on the roofs of residential houses right up to billion dollar solar farms with in excess of 1 million panels. We offer thermal image testing and bird proofing for our residential and commercial clients and thermal drone imaging services for our solar farm clients.
We vacuum clean roof gutters (using a LoftSuck) on the residential house next door right up to enormous private and public schools, colleges, shopping centres, strat complexes and commercial buildings.
When first built our business had more of a domestic residential skew and the website reflected that. While that is still part of our core business we are now bidding on and have secured large government, commercial and infrastructure contracts and our new website needs to reflect our growth and our new business. We need a new site that it optimised for both desktop ad phone viewing as our latest figures showed that 73% of people visiting our site are on mobile phones. We have an extensive amount of data on Tallymark Insights available as well as Bidlines. Both that would also need integrating with the site along with a few other plugins such as Quilro Chat IQ, Chatterbox etc along with SEO key words etc. We are also the winner and finalists over multiple years of the small business of the year awards and we like to proudly and prominently display those on our site.
We are looking for a new site with a modern professional feel / theme
There is a definitive break in our business between the solar Panel cleaning clients and the gutter cleaning clients so we would like a home page that begins with a simple choice:
Solar Panel Cleaning – Gutter Cleaning
With a professional full screen background image (we have hundreds to choose from) and along the bottom a small area with rights reserved etc, phone number etc (at some point in the future we will split these into two businesses but for now it’s what we have).
After that selection is made we would like a repeat of that same scenario but the selection is:
If it’s Solar Panel Cleaning
(new background image)
Government – Infrastructure – Commercial – Residential
If it’s Gutter Cleaning
(new background image)
Government – Strata – Commercial – Residential
After making those choices then onto the relevant pages with background images relevant to each sector and a them that suits (on the residential we would like to keep the link to our tallymark reviews) - We will provide copy / text for each relevant page.
Other than that, a menu inclusive of the above and:
Resellers Portal – we will provide a link to this from Quilro CRM)
Customer portal (we will supply a link to this from our booking system)
We also need a page for our Solar Resellers / Partners page but we will give them a link to this, it won’t be listed on the site.
Request a quote page (Again we will provide information from Quilro as this will be linked to the CRM)
Standard contact us page inclusive of phone numbers, address and fields supplied from CRM
Sydney – 02 7391 8056
Southern Highlands – 02 4863 1708
Goulburn – 02 4863 1708
Canberra – 02 6172 4385
Wollongong – 02 4239 5817
sales@brightleaf.com.au
Head Office - Moss Vale NSW 2577
ABN: 48093716552
Responsive Design: Optimized for desktop and mobile (73% mobile visitors).
Fast Loading Speed: Optimized for performance.
Smooth Transition Animations: For service and category selection.
Sticky Contact Bar: Always accessible at the bottom of mobile screens for quick calls.
SEO Optimization: Focused on government tenders, large-scale commercial contracts, and infrastructure projects.
Integrations
Tallymark Insights & Tallymark Bidlines.
Quilro Chat IQ.
Chatterbox Beacon.
SEO tools and keyword optimization.
Many many more images available if needed
Target Market(s)
Residential, commercial, Government

```html
<!DOCTYPE html>
<html lang="en">
<head>
<meta charset="utf-8">
<title>Brightleaf – Website Screens</title>
<link href="https://fonts.googleapis.com/css2?family=Cabin:wght@500;600;700&family=Lato:wght@400;700&display=swap" rel="stylesheet">
<style>
:root{
  --page:#ffffff;
  --sky:#2b8fd6;
  --ink:#1e1e1e;
  --rule:#cfcfcf;
  --white:#ffffff;
}
*{margin:0;padding:0;box-sizing:border-box}
html,body{width:1200px;height:296px;overflow:hidden;background:var(--page)}
body{position:relative;font-family:"Lato",sans-serif;color:var(--ink)}

.screen{position:absolute;top:10px;width:391px;height:276px;background:var(--white);box-shadow:0 0 3px rgba(0,0,0,.18);overflow:hidden}
.screen--home{left:6px;top:9px}
.screen--solar{left:404px}
.screen--gutter{left:803px}

.hero{position:absolute;left:0;top:0;width:391px;height:197px;overflow:hidden}
.hero__photo{position:absolute;top:0;height:100%}
.photo--roof-left{left:0;width:195px;background:linear-gradient(165deg,#2f5fb0 0%,#2a56a6 30%,#3a6dbd 52%,#27509f 70%,#1b3c86 88%,#284d96 100%)}
.photo--gutter-right{left:195px;width:196px;background:linear-gradient(160deg,#6e9fd8 0%,#4f86cf 22%,#7aa4d6 40%,#3d74c3 58%,#2d5fb3 78%,#8aa9cf 100%)}
.photo--solar-farm{left:0;width:100%;background:linear-gradient(172deg,#4c7f7a 0%,#3d6b8f 14%,#2f5da6 32%,#3d6fba 48%,#26499a 68%,#1f3f8c 84%,#2a4f99 100%)}
.photo--roof-gutter{left:0;width:100%;background:linear-gradient(125deg,#4f8cbf 0%,#3f7ab8 18%,#2f6bc2 38%,#2c5fb3 55%,#3a5f84 72%,#34566f 86%,#3f6478 100%)}

.brand{position:absolute;display:flex;align-items:center;gap:3px;font-family:"Cabin",sans-serif;font-weight:600;color:var(--white)}
.brand__dot{width:6px;height:6px;background:currentColor}
.hero .brand{left:36px;top:45px;font-size:11px}

.portal-nav{position:absolute;top:8px;left:232px;display:flex;gap:6px}
.portal-btn{width:58px;height:17px;border-radius:2px;font-family:"Cabin",sans-serif;font-weight:600;font-size:5.6px;display:flex;align-items:center;justify-content:center}
.portal-btn--solid{background:var(--white);color:var(--ink)}
.portal-btn--outline{border:1px solid var(--white);color:var(--white)}

.choice{position:absolute;font-family:"Cabin",sans-serif;font-weight:700;font-size:15px;line-height:18px;color:var(--white);text-decoration:underline;text-decoration-thickness:1px;text-underline-offset:1px}
.choice--solar{left:37px;top:152px}
.choice--gutter{left:210px;top:150px}

.hero__title{position:absolute;left:0;width:100%;top:90px;text-align:center;font-family:"Cabin",sans-serif;font-weight:700;font-size:21px;line-height:24px;color:var(--white)}
.sector-nav{position:absolute;left:0;width:100%;top:121px;display:flex;justify-content:center;gap:11px;font-family:"Cabin",sans-serif;font-weight:600;font-size:8px;color:var(--white)}

.footer{position:absolute;left:0;top:197px;width:391px;height:79px}
.footer .brand{left:37px;top:40px;color:var(--sky);font-size:7px}
.footer .brand__dot{width:4px;height:4px}
.abn{position:absolute;left:37px;top:51px;font-size:4.2px;color:var(--ink)}
.contact-labels{position:absolute;left:106px;top:20px}
.contact-label{display:flex;align-items:center;gap:4px;height:12.5px;font-size:6.4px;color:var(--ink)}
.contact-label svg{width:8px;height:8px}
.offices{position:absolute;left:165px;top:23px;width:200px;height:30px}
.office{position:absolute;font-size:4.2px;color:var(--ink);white-space:nowrap}
.office span{display:block;line-height:5px}
.office span+span{margin-top:7px}
.email{position:absolute;left:165px;top:48px;font-size:4.2px}
.socials{position:absolute;left:325px;top:51px;display:flex;gap:3px}
.social{width:7px;height:7px;border-radius:50%;border:.7px solid var(--sky)}
.social--filled{background:var(--sky)}
.footer__rule{position:absolute;left:37px;width:318px;top:67px;border-top:.6px solid var(--rule)}
.copyright{position:absolute;left:0;width:391px;top:70px;text-align:center;font-size:4.2px}
</style>
</head>
<body>

<section class="screen screen--home">
  <div class="hero">
    <div class="hero__photo photo--roof-left" role="img" aria-label="Worker in high-visibility vest cleaning rooftop solar panels with a long pole, blue tint"></div>
    <div class="hero__photo photo--gutter-right" role="img" aria-label="Worker on a ladder cleaning a roof gutter, blue tint"></div>
    <div class="brand"><span class="brand__dot"></span>Brightleaf</div>
    <nav class="portal-nav"><span class="portal-btn portal-btn--solid">RESELLERS PORTAL</span><span class="portal-btn portal-btn--outline">CUSTOMER PORTAL</span></nav>
    <a class="choice choice--solar">SOLAR PANEL<br>CLEANING</a>
    <a class="choice choice--gutter">GUTTER<br>CLEANING</a>
  </div>
  <footer class="footer">
    <div class="brand"><span class="brand__dot"></span>Brightleaf</div>
    <div class="abn"><b>ABN</b>&nbsp; 48093716552</div>
    <div class="contact-labels">
      <div class="contact-label"><svg viewBox="0 0 10 10"><circle cx="5" cy="5" r="5" fill="#2b8fd6"/><circle cx="5" cy="4.3" r="1.6" fill="#fff"/></svg>Our Location</div>
      <div class="contact-label"><svg viewBox="0 0 10 10"><circle cx="5" cy="5" r="5" fill="#2b8fd6"/><path d="M3.3 2.8l1 1-.5.8a4 4 0 0 0 1.6 1.6l.8-.5 1 1-.7.8C4.5 7.3 2.7 5.5 2.5 3.5z" fill="#fff"/></svg>Call Us</div>
      <div class="contact-label"><svg viewBox="0 0 10 10"><circle cx="5" cy="5" r="5" fill="#2b8fd6"/><rect x="2.6" y="3.3" width="4.8" height="3.4" fill="#fff"/><path d="M2.6 3.3L5 5.2l2.4-1.9" stroke="#2b8fd6" stroke-width=".5" fill="none"/></svg>Mail Us</div>
    </div>
    <div class="offices">
      <div class="office" style="left:0"><span>Sydney</span><span>02 7391 8056</span></div>
      <div class="office" style="left:39px"><span>Southern Highlands</span><span>02 4863 1708</span></div>
      <div class="office" style="left:83px"><span>Goulburn</span><span>02 4863 1708</span></div>
      <div class="office" style="left:120px"><span>Canberra</span><span>02 6172 4385</span></div>
      <div class="office" style="left:157px"><span>Wollongong</span><span>02 4239 5817</span></div>
    </div>
    <div class="email">sales@brightleaf.com.au</div>
    <div class="socials"><span class="social social--filled"></span><span class="social"></span><span class="social"></span></div>
    <div class="footer__rule"></div>
    <div class="copyright"><b>Copyright © 2025 Brightleaf . All rights reserved.</b></div>
  </footer>
</section>

<section class="screen screen--solar">
  <div class="hero">
    <div class="hero__photo photo--solar-farm" role="img" aria-label="Team of workers in hard hats washing rows of solar panels at a solar farm, blue tint"></div>
    <div class="brand"><span class="brand__dot"></span>Brightleaf</div>
    <nav class="portal-nav"><span class="portal-btn portal-btn--solid">RESELLERS PORTAL</span><span class="portal-btn portal-btn--outline">CUSTOMER PORTAL</span></nav>
    <h1 class="hero__title">SOLAR PANEL CLEANING</h1>
    <nav class="sector-nav"><span>Government</span><span>Infrastructure</span><span>Commercial</span><span>Residential</span></nav>
  </div>
  <footer class="footer">
    <div class="brand"><span class="brand__dot"></span>Brightleaf</div>
    <div class="abn"><b>ABN</b>&nbsp; 48093716552</div>
    <div class="contact-labels">
      <div class="contact-label"><svg viewBox="0 0 10 10"><circle cx="5" cy="5" r="5" fill="#2b8fd6"/><circle cx="5" cy="4.3" r="1.6" fill="#fff"/></svg>Our Location</div>
      <div class="contact-label"><svg viewBox="0 0 10 10"><circle cx="5" cy="5" r="5" fill="#2b8fd6"/><path d="M3.3 2.8l1 1-.5.8a4 4 0 0 0 1.6 1.6l.8-.5 1 1-.7.8C4.5 7.3 2.7 5.5 2.5 3.5z" fill="#fff"/></svg>Call Us</div>
      <div class="contact-label"><svg viewBox="0 0 10 10"><circle cx="5" cy="5" r="5" fill="#2b8fd6"/><rect x="2.6" y="3.3" width="4.8" height="3.4" fill="#fff"/><path d="M2.6 3.3L5 5.2l2.4-1.9" stroke="#2b8fd6" stroke-width=".5" fill="none"/></svg>Mail Us</div>
    </div>
    <div class="offices">
      <div class="office" style="left:0"><span>Sydney</span><span>02 7391 8056</span></div>
      <div class="office" style="left:39px"><span>Southern Highlands</span><span>02 4863 1708</span></div>
      <div class="office" style="left:83px"><span>Goulburn</span><span>02 4863 1708</span></div>
      <div class="office" style="left:120px"><span>Canberra</span><span>02 6172 4385</span></div>
      <div class="office" style="left:157px"><span>Wollongong</span><span>02 4239 5817</span></div>
    </div>
    <div class="email">sales@brightleaf.com.au</div>
    <div class="socials"><span class="social social--filled"></span><span class="social"></span><span class="social"></span></div>
    <div class="footer__rule"></div>
    <div class="copyright"><b>Copyright © 2025 Brightleaf . All rights reserved.</b></div>
  </footer>
</section>

<section class="screen screen--gutter">
  <div class="hero">
    <div class="hero__photo photo--roof-gutter" role="img" aria-label="Worker in safety harness cleaning a mossy tiled roof and gutter beside trees, blue tint"></div>
    <div class="brand"><span class="brand__dot"></span>Brightleaf</div>
    <nav class="portal-nav"><span class="portal-btn portal-btn--solid">RESELLERS PORTAL</span><span class="portal-btn portal-btn--outline">CUSTOMER PORTAL</span></nav>
    <h1 class="hero__title">GUTTER CLEANING</h1>
    <nav class="sector-nav"><span>Government</span><span>Strata</span><span>Commercial</span><span>Residential</span></nav>
  </div>
  <footer class="footer">
    <div class="brand"><span class="brand__dot"></span>Brightleaf</div>
    <div class="abn"><b>ABN</b>&nbsp; 48093716552</div>
    <div class="contact-labels">
      <div class="contact-label"><svg viewBox="0 0 10 10"><circle cx="5" cy="5" r="5" fill="#2b8fd6"/><circle cx="5" cy="4.3" r="1.6" fill="#fff"/></svg>Our Location</div>
      <div class="contact-label"><svg viewBox="0 0 10 10"><circle cx="5" cy="5" r="5" fill="#2b8fd6"/><path d="M3.3 2.8l1 1-.5.8a4 4 0 0 0 1.6 1.6l.8-.5 1 1-.7.8C4.5 7.3 2.7 5.5 2.5 3.5z" fill="#fff"/></svg>Call Us</div>
      <div class="contact-label"><svg viewBox="0 0 10 10"><circle cx="5" cy="5" r="5" fill="#2b8fd6"/><rect x="2.6" y="3.3" width="4.8" height="3.4" fill="#fff"/><path d="M2.6 3.3L5 5.2l2.4-1.9" stroke="#2b8fd6" stroke-width=".5" fill="none"/></svg>Mail Us</div>
    </div>
    <div class="offices">
      <div class="office" style="left:0"><span>Sydney</span><span>02 7391 8056</span></div>
      <div class="office" style="left:39px"><span>Southern Highlands</span><span>02 4863 1708</span></div>
      <div class="office" style="left:83px"><span>Goulburn</span><span>02 4863 1708</span></div>
      <div class="office" style="left:120px"><span>Canberra</span><span>02 6172 4385</span></div>
      <div class="office" style="left:157px"><span>Wollongong</span><span>02 4239 5817</span></div>
    </div>
    <div class="email">sales@brightleaf.com.au</div>
    <div class="socials"><span class="social social--filled"></span><span class="social"></span><span class="social"></span></div>
    <div class="footer__rule"></div>
    <div class="copyright"><b>Copyright © 2025 Brightleaf . All rights reserved.</b></div>
  </footer>
</section>

</body>
</html>
```